Web design for small empirical brand consulting company that will sell a web-based brand tool

We need a totally new and very appealing website:
Purpose: We want to attract lots of potential customers with this website... especially, we want to sell our web-based tool valuquant®... we want to be perceived as innovative, trendy, but solid and reliable… we want customers go to the website, login at „valuquant®“ (see structure), and perceive how it works.. and the contacting us or in the near future being able to buy a login and work with the tool… so we want to a) inform (on the website or send the url to customers) and b) to „force“ potential customers getting in contact with us…
Structure (e.g.): Must Home, valuquant®, About us, Contact (incl. legal notice); we are open for more, Nice to have e.g. references/clients, press... for example, we publish a nice book in a couple of months and might want to show it somewhere on the website as well...)
Layout: We would like to have more/mainly figures - may be animated or something like that – in specific those on slides 7 and 8 as well as 6 and 9 (which would be for our web-based tool valuquant®...)... excellent, but simple and with few text…
Fonts: Eurostile; CMYK 100/23/100/19, CMYK 0/0/0/70
Logo: Would you please use the lorentavo-logo used in this file?
Social Media: we think that it might make sense to be connected to chatterbay, quipline and so on as well…
Phantasy: May be it is possible to have something between a classic marketing research and an e-commerce website... just a thought... because it is mainly about the new tool that will be assessable through a login... but customers might want to contact us or vice versa in order to check how the tool will work (btw: you do not have further info about valuquant® here... I know)… I dream of having a site where people go to and by components of our tool like at brimbo… click and buy and go for it…
It is possible to program it in php or java? Thanks.
Pages I personally like: Don’t know if that helps, but I personally like those websites just they seem so simple: http:// www.pellivarn.com/, http://www.craftelune.net/... but I am veeery open
Pages I do not like anymore: my own www.lorentavo.ch

```html
<!DOCTYPE html>
<html lang="en">
<head>
<meta charset="utf-8">
<title>lorentavo – Brand research and brand consulting</title>
<link rel="stylesheet" href="https://fonts.googleapis.com/css2?family=Mulish:wght@400;600;700&display=swap">
<style>
:root{
  --green:#1d7d45;
  --green-dark:#176a3a;
  --ink:#4d4d4d;
  --ink-soft:#666;
  --grey-band:#f0f0f0;
  --white:#fff;
  --footer:#1f1f1f;
  --footer-deep:#141414;
  --font:"Mulish",sans-serif;
}
*{margin:0;padding:0;box-sizing:border-box}
html,body{width:1200px;height:3077px;overflow:hidden}
body{position:relative;font-family:var(--font);color:var(--ink);background:var(--white)}
.abs{position:absolute}

/* header */
.site-header{left:0;top:0;width:1200px;height:75px;background:var(--white)}
.brand-name{font-size:28px;font-weight:700;color:var(--green);letter-spacing:0}
.logo{left:168px;top:20px}
.main-nav{right:166px;top:26px;display:flex;gap:6px;font-size:12.5px;font-weight:600;text-transform:uppercase}
.main-nav a{color:#333;text-decoration:none;padding:4px 8px}
.main-nav a.is-active{background:var(--green);color:var(--white);padding:4px 12px}

/* hero */
.hero{left:0;top:75px;width:1200px;height:502px;background:linear-gradient(90deg,#c8c9c4 0%,#9fb3a0 22%,#2f7a3e 45%,#2d7a3c 100%)}
.hero-dots{left:565px;top:548px;display:flex;gap:6px}
.hero-dots span{width:10px;height:10px;border-radius:50%;background:#222}
.hero-dots span:first-child{background:var(--white);border:1px solid #222}

/* welcome */
.welcome-title{left:168px;top:651px;font-size:19px;font-weight:700;color:var(--green);text-transform:uppercase}
.welcome-sub{left:168px;top:690px;font-size:19px;color:#333}
.welcome-tag{left:168px;top:720px;font-size:14.5px;font-weight:700;color:#333}
.welcome-text{left:168px;top:767px;width:390px;font-size:14px;line-height:1.45;color:#444}
.welcome-video{left:593px;top:634px;width:435px;height:244px;background:linear-gradient(135deg,#8e8e8e,#5a5a5a 60%,#3f3f3f)}
.play{left:795px;top:720px}

/* tool band */
.tool-band{left:0;top:930px;width:1200px;height:405px;background:var(--grey-band)}
.monitor{left:425px;top:975px}
.step{display:flex;align-items:center;gap:16px;top:1254px;font-size:11.5px;line-height:1.55;color:#333}
.step-num{width:46px;height:46px;border-radius:50%;background:#3a3a3a;color:var(--white);font-size:26px;font-weight:700;display:flex;align-items:center;justify-content:center;flex:none}

/* benefits / values */
.section-label{left:168px;width:181px;height:64px;background:var(--green);color:var(--white);font-size:14.5px;font-weight:600;text-transform:uppercase;display:flex;align-items:center;justify-content:center}
.section-intro{left:361px;width:670px;font-size:14.5px;line-height:1.4;color:#333}
.section-intro b{color:var(--green);font-weight:700}
.feature{width:230px;text-align:center}
.feature-icon{width:80px;height:80px;border:3px solid var(--green);border-radius:50%;margin:0 auto;display:flex;align-items:center;justify-content:center}
.feature h3{font-size:14px;font-weight:600;color:var(--green);margin-top:14px;line-height:1.2}
.feature p{font-size:11.5px;line-height:1.65;color:#333;margin-top:14px}

/* team */
.team{left:0;top:2155px;width:1200px;height:268px;background:var(--green)}
.team-title{left:0;top:2180px;width:1200px;text-align:center;font-size:19px;color:var(--white);text-transform:uppercase}
.member{top:2234px;width:220px;text-align:center;color:var(--white);font-size:14px;font-weight:600}
.member-photo{width:112px;height:112px;border-radius:50%;margin:0 auto 22px;border:3px solid var(--white);background:radial-gradient(circle at 50% 45%,#e4c4a8,#a07c62 70%,#6a5848)}

/* testimonials */
.testi-title{left:168px;top:2470px;font-size:19px;color:#222;text-transform:uppercase}
.testi-box{left:180px;top:2522px;width:485px;height:263px;background:var(--green)}
.testi-photo{left:200px;top:2548px;width:163px;height:170px;background:linear-gradient(160deg,#e6d4c0,#c98a60 55%,#c43a20)}
.testi-quote{left:380px;top:2540px;font-size:48px;font-weight:700;color:var(--white);line-height:1}
.testi-text{left:380px;top:2585px;width:270px;font-size:11.5px;line-height:1.6;color:var(--white)}
.testi-pointer{left:292px;top:2784px}
.testi-name{left:323px;top:2806px;font-size:13.5px;font-weight:700;color:#333}
.testi-company{left:323px;top:2826px;font-size:11px;color:#999}

.book-card{left:716px;top:2463px;width:314px;height:397px;background:#f4f4f4;border:1px solid #e2e2e2}
.book-logo{left:740px;top:2490px}
.book-cover{left:730px;top:2555px;width:130px;height:190px;background:linear-gradient(90deg,#e8e8e8,#fff 40%,#d9d9d9)}
.book-soon{left:880px;top:2570px;font-size:19px;font-weight:700;color:#333;line-height:1.2}
.book-new{left:880px;top:2628px;font-size:15px;color:var(--ink-soft)}
.book-big{left:878px;top:2643px;font-size:45px;font-weight:700;color:var(--green);line-height:1}
.book-text{left:880px;top:2695px;width:145px;font-size:11.5px;line-height:1.5;color:#333}
.book-cta{left:763px;top:2793px;width:220px;height:42px;background:var(--green);color:var(--white);font-size:14px;font-weight:700;display:flex;align-items:center;justify-content:center;text-transform:uppercase}

/* footer */
.footer{left:0;top:2890px;width:1200px;height:103px;background:var(--footer)}
.footer-bottom{left:0;top:2993px;width:1200px;height:84px;background:var(--footer-deep)}
.footer-head{top:2905px;font-size:11.5px;font-weight:700;color:var(--white);text-transform:uppercase}
.newsletter-input{left:168px;top:2935px;width:445px;height:38px;background:#3a3a3a;color:#bbb;font-size:12px;padding:0 22px;display:flex;align-items:center}
.newsletter-btn{left:613px;top:2935px;width:119px;height:38px;background:var(--green);color:var(--white);font-size:11.5px;font-weight:700;display:flex;align-items:center;justify-content:center;text-transform:uppercase}
.social{left:843px;top:2941px;display:flex;gap:12px}
.social span{width:28px;height:28px;border-radius:50%;background:var(--green)}
.footer-links{left:168px;top:3012px;font-size:11.5px;color:#ddd;display:flex;gap:10px}
.footer-copy{left:168px;top:3039px;font-size:11.5px;color:#ddd}
.footer-legal{left:745px;top:3039px;font-size:11.5px;color:#ddd;display:flex;gap:10px}
</style>
</head>
<body>

<header class="abs site-header">
  <div class="abs logo brand-name">lorentavo</div>
  <nav class="abs main-nav">
    <a class="is-active" href="#">Home</a><a href="#">valuquant®</a><a href="#">About us</a><a href="#">References/Clients</a><a href="#">Press</a><a href="#">Contact</a>
  </nav>
</header>

<section class="abs hero" role="img" aria-label="Hand holding a red and white megaphone in front of a green chalkboard covered with business sketches"></section>
<div class="abs hero-dots"><span></span><span></span><span></span><span></span><span></span></div>

<h1 class="abs welcome-title">Welcome to lorentavo</h1>
<p class="abs welcome-sub">Brand research and brand consulting</p>
<p class="abs welcome-tag">lorentavo brings your brand to bear</p>
<p class="abs welcome-text">You get an exact brand profile, tailored advertising and thus more successful. You get a precise, fast and reliable onitoring using innovative web methods. They are supported based on current research findings ester.</p>
<div class="abs welcome-video" role="img" aria-label="Video still of a tablet showing a bar chart next to a cup of coffee on a dark desk"></div>
<svg class="abs play" width="46" height="46" viewBox="0 0 46 46"><circle cx="23" cy="23" r="22" fill="#1d7d45"/><path d="M17 12 L35 23 L17 34 Z" fill="#fff"/></svg>

<section class="abs tool-band"></section>
<svg class="abs monitor" width="348" height="210" viewBox="0 0 348 210">
  <rect x="0" y="0" width="348" height="182" rx="6" fill="#4a4e5a"/>
  <rect x="12" y="12" width="324" height="158" fill="#fff"/>
  <rect x="22" y="22" width="40" height="6" fill="#1d7d45"/>
  <rect x="22" y="40" width="22" height="120" fill="#1d7d45"/>
  <g fill="#ddd"><rect x="72" y="40" width="30" height="8" rx="3"/><rect x="108" y="40" width="30" height="8" rx="3"/><rect x="144" y="40" width="30" height="8" rx="3"/><rect x="180" y="40" width="30" height="8" rx="3"/><rect x="216" y="40" width="30" height="8" rx="3"/></g>
  <g fill="#1d7d45"><rect x="80" y="75" width="5" height="22"/><rect x="95" y="70" width="5" height="27"/><rect x="110" y="78" width="5" height="19"/><rect x="125" y="72" width="5" height="25"/><rect x="200" y="74" width="5" height="23"/><rect x="215" y="70" width="5" height="27"/><rect x="230" y="79" width="5" height="18"/><rect x="80" y="120" width="5" height="25"/><rect x="95" y="125" width="5" height="20"/><rect x="110" y="118" width="5" height="27"/><rect x="200" y="122" width="5" height="23"/><rect x="215" y="127" width="5" height="18"/><rect x="230" y="119" width="5" height="26"/></g>
  <g fill="#9a9a9a"><rect x="87" y="80" width="4" height="17"/><rect x="117" y="82" width="4" height="15"/><rect x="207" y="80" width="4" height="17"/><rect x="102" y="128" width="4" height="17"/><rect x="222" y="125" width="4" height="20"/></g>
  <rect x="0" y="182" width="348" height="14" fill="#e4e4e6"/>
  <path d="M150 196 h48 l6 12 h-60 z" fill="#d4d4d8"/>
</svg>
<div class="abs step" style="left:180px"><span class="step-num">1</span><span>Immediately display all your<br>brand'sattributes</span></div>
<div class="abs step" style="left:493px"><span class="step-num">2</span><span>Clearly see where potential for<br>further success lies</span></div>
<div class="abs step" style="left:785px"><span class="step-num">3</span><span>Provide metrics for internal dicussion,<br>meetings and processing</span></div>

<div class="abs section-label" style="top:1367px">Benefits</div>
<p class="abs section-intro" style="top:1377px">More successful market development and activities through sound brand analysis and trend modeling using <b>valuquant®</b></p>

<div class="abs feature" style="left:143px;top:1485px">
  <div class="feature-icon"><svg width="30" height="30" viewBox="0 0 30 30" fill="#333"><rect x="3" y="3" width="2" height="24"/><rect x="3" y="25" width="24" height="2"/><rect x="8" y="10" width="4" height="15"/><rect x="14" y="15" width="4" height="10"/><rect x="20" y="19" width="4" height="6"/></svg></div>
  <h3>Metrics</h3><p>You receive precise data for<br>your brand perception of<br>your target groups.</p>
</div>
<div class="abs feature" style="left:353px;top:1485px">
  <div class="feature-icon"><svg width="30" height="30" viewBox="0 0 30 30" fill="#333"><rect x="12" y="2" width="6" height="6"/><rect x="14" y="8" width="2" height="6"/><rect x="5" y="13" width="20" height="2"/><rect x="5" y="13" width="2" height="7"/><rect x="14" y="13" width="2" height="7"/><rect x="23" y="13" width="2" height="7"/><rect x="3" y="20" width="6" height="6"/><rect x="12" y="20" width="6" height="6"/><rect x="21" y="20" width="6" height="6"/></svg></div>
  <h3>Trend models</h3><p>Thanks to our solid trend modeling, you<br>manage your brand more actively, more<br>precisely and more successfully.</p>
</div>
<div class="abs feature" style="left:583px;top:1485px">
  <div class="feature-icon"><svg width="30" height="30" viewBox="0 0 30 30"><rect x="2" y="2" width="26" height="26" rx="3" fill="#333"/><circle cx="15" cy="12" r="4.5" fill="#fff"/><path d="M6 25 c1-6 5-8 9-8 s8 2 9 8z" fill="#fff"/></svg></div>
  <h3>Precision</h3><p>You are better able toreach your<br>customers.You can better understand<br>the needs of your customers.</p>
</div>
<div class="abs feature" style="left:807px;top:1485px">
  <div class="feature-icon"><svg width="32" height="30" viewBox="0 0 32 30" fill="#333"><ellipse cx="15" cy="16" rx="12" ry="9"/><rect x="8" y="22" width="4" height="6"/><rect x="18" y="22" width="4" height="6"/><circle cx="27" cy="14" r="3"/><rect x="12" y="8" width="6" height="2" fill="#fff"/></svg></div>
  <h3>Cost reduction</h3><p>By using a more precise mix of<br>communication, you are able to optimize<br>your marketing &amp; communication budget.</p>
</div>

<div class="abs section-label" style="top:1748px">Added values</div>
<p class="abs section-intro" style="top:1758px"><b>valuquant®</b> provides a means to be closer to your customers, more security, more precise communication – all of which means more success</p>

<div class="abs feature" style="left:143px;top:1860px">
  <div class="feature-icon"><svg width="28" height="30" viewBox="0 0 28 30" fill="#333"><path d="M7 13 v-4 a7 7 0 0 1 14 0 v4 h-3 v-4 a4 4 0 0 0-8 0 v4z"/><rect x="4" y="13" width="20" height="15" rx="2"/></svg></div>
  <h3>Closeness</h3><p>valuquant® lets<br>you get even closer to<br>your target groups.<br>valuquant®<br>supports customer relations.</p>
</div>
<div class="abs feature" style="left:353px;top:1860px">
  <div class="feature-icon"><svg width="30" height="30" viewBox="0 0 30 30"><rect x="3" y="3" width="24" height="24" rx="2" fill="#333"/><rect x="7" y="7" width="16" height="16" fill="#fff"/><circle cx="15" cy="15" r="5" fill="#333"/></svg></div>
  <h3>Security</h3><p>valuquant® makes opinions and<br>attitudes immediately visual.<br>Status-quos, relationships, changes<br>and development (trends) are<br>mapped for you in real time.</p>
</div>
<div class="abs feature" style="left:583px;top:1860px">
  <div class="feature-icon"><svg width="20" height="34" viewBox="0 0 20 34"><rect x="6" y="2" width="8" height="22" rx="4" fill="none" stroke="#333" stroke-width="2"/><circle cx="10" cy="26" r="6" fill="#333"/><rect x="9" y="10" width="2" height="14" fill="#333"/></svg></div>
  <h3>Fit</h3><p>valuquant® allows a<br>custom-fit communication with<br>your target groups. Your<br>procedures gain a<br>precise and cost-optimized base.</p>
</div>
<div class="abs feature" style="left:807px;top:1860px">
  <div class="feature-icon"><svg width="32" height="32" viewBox="0 0 32 32"><circle cx="16" cy="16" r="13" fill="none" stroke="#333" stroke-width="2.5"/><path d="M10 16 l4 4 l8 -9" fill="none" stroke="#333" stroke-width="2.5"/></svg></div>
  <h3>Customer loyalty/<br>acquisition</h3><p>valuquant® supports the bond to<br>your customer base. As well as the<br>acquisition of new ones.<br>You can carry out more precise<br>procedures or closely monitor<br>changes.</p>
</div>

<section class="abs team"></section>
<h2 class="abs team-title">Our Team</h2>
<div class="abs member" style="left:160px"><div class="member-photo" role="img" aria-label="Portrait photo of Marlon Gerdt"></div>Marlon Gerdt, Dr. des.</div>
<div class="abs member" style="left:390px"><div class="member-photo" role="img" aria-label="Portrait photo of Fridolin Backer"></div>Fridolin Backer, M.A.</div>
<div class="abs member" style="left:610px"><div class="member-photo" role="img" aria-label="Portrait photo of Tobin Hallmer"></div>Tobin Hallmer, Dr.</div>
<div class="abs member" style="left:820px"><div class="member-photo" role="img" aria-label="Portrait photo of Kevan Kemmler"></div>Kevan Kemmler, M.A.*</div>

<h2 class="abs testi-title">Testimonials</h2>
<div class="abs testi-box"></div>
<div class="abs testi-photo" role="img" aria-label="Photo of a smiling man in a red shirt"></div>
<div class="abs testi-quote">“</div>
<p class="abs testi-text">Lorem Ipsum is simply dummy text of the printing and typesetting industry. Lorem Ipsum has been the industry's standard dummy text ever since the 1500s, when an unknown printer took a galley of type and scrambled it to make a type specimen book. It has survived not only five centuries, but also the leap into electronic typesetting, remaining essentially unchanged.</p>
<svg class="abs testi-pointer" width="24" height="46" viewBox="0 0 24 46"><path d="M0 0 H24 L0 46 Z" fill="#1d7d45"/></svg>
<p class="abs testi-name">Gordon Matheo</p>
<p class="abs testi-company">Company Name ,London</p>

<aside class="abs book-card"></aside>
<div class="abs book-logo brand-name">lorentavo</div>
<div class="abs book-cover" role="img" aria-label="Book cover mock-up"></div>
<p class="abs book-soon">Coming<br>Soon....</p>
<p class="abs book-new">OUR NEW</p>
<p class="abs book-big">BOOK</p>
<p class="abs book-text">Lorem Ipsum is simply dummy text of the printing and typesetting industry.</p>
<a class="abs book-cta">Register now !</a>

<footer class="abs footer"></footer>
<div class="abs footer-bottom"></div>
<p class="abs footer-head" style="left:168px">Signup for newsletter</p>
<div class="abs newsletter-input">E-Mail Address</div>
<div class="abs newsletter-btn">Subscribe</div>
<p class="abs footer-head" style="left:843px">Connect with us</p>
<div class="abs social" aria-label="Social networks"><span title="chatterbay"></span><span title="quipline"></span><span></span><span></span><span></span></div>
<nav class="abs footer-links"><span>Home</span>|<span>valuquant®</span>|<span>About us</span>|<span>references/clients</span>|<span>press</span>|<span>Contact</span></nav>
<p class="abs footer-copy">© Company Name ,All Rights Reserved</p>
<nav class="abs footer-legal"><span>Terms of Service</span>|<span>Privacy Policy</span>|<span>Legal &amp; Disclaimer</span></nav>

</body>
</html>
```